Mindfulness School for Children -- Business Cards

We're looking for business cards for our school directors and owners. We're a mindfulness school for children called little lanterns. Attached are our logos/icons.

```html
<!DOCTYPE html>
<html lang="en">
<head>
<meta charset="utf-8">
<title>little lanterns – Business Card</title>
<link rel="stylesheet" href="https://fonts.googleapis.com/css2?family=Arimo:wght@400;700&display=swap">
<style>
  :root {
    --backdrop: #e6e7e8;
    --card: #ffffff;
    --teal: #3aa3b8;
    --teal-dark: #2b8ea4;
    --green: #8fd3a4;
    --mint: #c4ead0;
    --sky: #9fd1df;
    --ink: #1f1f1f;
    --faint: #f3f4f4;
    --back-dark: #1c1c1e;
    --back-mid: #2e2e30;
    --back-light: #6c6c6e;
  }
  * { box-sizing: border-box; margin: 0; padding: 0; }
  html, body { width: 1200px; height: 900px; overflow: hidden; }
  body {
    background: var(--backdrop);
    font-family: "Arimo", Arial, sans-serif;
    display: flex; flex-direction: column;
    align-items: center; justify-content: center; gap: 40px;
  }
  .business-card {
    position: relative;
    width: 660px; height: 378px;
    overflow: hidden;
  }

  /* Front */
  .card-front { background: var(--card); }
  .brand-mark {
    position: absolute; left: 52px; top: 46px;
    display: flex; align-items: center; gap: 10px;
  }
  .brand-dot {
    width: 14px; height: 14px; border-radius: 50%;
    background: var(--teal);
  }
  .brand-name {
    font-weight: 700; font-size: 36px; letter-spacing: 0.3px;
    color: var(--teal);
  }
  .faint-mark {
    position: absolute; left: 330px; top: 210px;
    width: 250px; height: 250px; border-radius: 50%;
    background: var(--faint);
  }
  .contact-block {
    position: absolute; left: 52px; top: 188px;
    font-style: normal;
    font-size: 15px; line-height: 22px; color: var(--ink);
  }
  .contact-address { margin-bottom: 4px; }
  .contact-line { display: flex; align-items: center; gap: 8px; }
  .contact-line svg { width: 12px; height: 12px; flex: none; fill: var(--teal); }
  .person {
    position: absolute; right: 46px; top: 196px;
    text-align: right; padding-right: 14px;
  }
  .person::after {
    content: ""; position: absolute; right: 0; top: 4px;
    width: 5px; height: 46px;
    background: linear-gradient(180deg, var(--teal), var(--green));
  }
  .person-name {
    font-weight: 700; font-size: 25px; letter-spacing: 0.6px;
    color: var(--teal-dark);
  }
  .person-title { font-size: 15px; color: var(--ink); margin-top: 4px; }
  .edge-band {
    position: absolute; left: 0; right: 0; bottom: 0; height: 8px;
    background: linear-gradient(90deg, var(--teal) 0%, var(--green) 50%, var(--mint) 75%, var(--sky) 100%);
  }

  /* Back */
  .card-back { background: var(--back-dark); }
  .back-pattern {
    position: absolute; inset: 0;
    background: linear-gradient(120deg, var(--back-dark) 0%, var(--back-mid) 45%, var(--back-light) 100%);
  }
  .back-brand {
    position: absolute; right: 56px; bottom: 52px;
    font-weight: 700; font-size: 24px; color: var(--teal);
  }
</style>
</head>
<body>
  <article class="business-card card-front">
    <div class="faint-mark" aria-hidden="true"></div>

    <header class="brand-mark">
      <span class="brand-dot" aria-hidden="true"></span>
      <span class="brand-name">little lanterns</span>
    </header>

    <address class="contact-block">
      <div class="contact-address">PO Box 4120 Cedar Lane<br>Region Name, CD 21096</div>
      <div class="contact-line">
        <svg viewBox="0 0 24 24"><path d="M6.6 10.8a15.1 15.1 0 0 0 6.6 6.6l2.2-2.2a1 1 0 0 1 1-.25 11.4 11.4 0 0 0 3.6.57 1 1 0 0 1 1 1V20a1 1 0 0 1-1 1A17 17 0 0 1 3 4a1 1 0 0 1 1-1h3.5a1 1 0 0 1 1 1c0 1.25.2 2.45.57 3.57a1 1 0 0 1-.25 1z"/></svg>
        <span>(00) 3920 6614</span>
      </div>
      <div class="contact-line">
        <svg viewBox="0 0 24 24"><path d="M7 2h10a2 2 0 0 1 2 2v16a2 2 0 0 1-2 2H7a2 2 0 0 1-2-2V4a2 2 0 0 1 2-2zm0 3v13h10V5z"/></svg>
        <span>(00) 2281 5073</span>
      </div>
      <div class="contact-line">
        <svg viewBox="0 0 24 24"><path d="M2 5h20v14H2zm2 2v.5l8 5 8-5V7zm0 2.9V17h16V9.9l-8 5z"/></svg>
        <span>hello@littlelanterns.com</span>
      </div>
      <div class="contact-line">
        <svg viewBox="0 0 24 24"><circle cx="12" cy="12" r="10"/></svg>
        <span>www.littlelanterns.com</span>
      </div>
    </address>

    <div class="person">
      <div class="person-name">NORA WHITFIELD</div>
      <div class="person-title">CEO/Founder</div>
    </div>

    <div class="edge-band" aria-hidden="true"></div>
  </article>

  <article class="business-card card-back">
    <div class="back-pattern" role="img" aria-label="Repeating flower pattern in glossy black and silver tones"></div>
    <span class="back-brand">little lanterns</span>
  </article>
</body>
</html>
```